New web design for a service provider in the medical field

We are looking for a new design for our website. We are a company that repairs and sells medical endoscopes. Our customers include doctors and hospitals. Our current website can be found at https://lumavex.de/en/lumavex-english.
We need a new web design (without programming) for the following 3 pages:
-Startpage https://lumavex.de/en/lumavex-english/
-Used endoscopes https://lumavex.de/en/used-endoscopes/
-Purchase https://lumavex.de/en/purchase/
The design should be modern and stylish.
The blue color of the logo should be reflected on the page, but not too intrusive.
I have uploaded the images from the header. If more images are needed, let me know and I will upload them.

Target Market(s)
Doctors and hospitals

```html
<!DOCTYPE html>
<html lang="en">
<head>
<meta charset="utf-8">
<title>Lumavex – Pick-up Order</title>
<link href="https://fonts.googleapis.com/css2?family=Barlow:wght@400;500;600;700&family=Jost:wght@400;500&display=swap" rel="stylesheet">
<style>
:root{
  --blue:#29a8e0;
  --navy:#1f3344;
  --text:#3a4550;
  --muted:#7a8590;
  --line:#c9d2d9;
  --form-bg:#eef5f9;
  --white:#fff;
}
*{box-sizing:border-box;margin:0;padding:0}
html,body{width:1200px;height:2930px;overflow:hidden}
body{position:relative;font-family:"Barlow",sans-serif;color:var(--navy);background:var(--white)}
.abs{position:absolute}
.topbar{left:0;top:0;width:1200px;height:33px;background:var(--blue);color:var(--white);font-weight:700;font-size:13px}
.topbar .follow{left:101px;top:10px}
.dot{display:inline-block;border-radius:50%;background:var(--white)}
.topbar .links{right:120px;top:0;display:flex;height:33px}
.topbar .links span{padding:10px 16px;border-left:1px solid rgba(255,255,255,.35)}
.topbar .links span:first-child{border-left:none}
.brand{font-family:"Barlow",sans-serif;font-weight:600;color:var(--navy);font-size:24px;display:flex;align-items:center;gap:8px}
.brand i{width:14px;height:14px;border-radius:50%;background:var(--blue);display:block}
.contact{font-size:14px;display:flex;gap:8px;align-items:center}
.contact .ico{width:22px;height:22px;border-radius:50%;background:var(--blue)}
.contact small{display:block;color:var(--blue);font-size:10px;font-weight:500}
.nav{top:111px;left:285px;display:flex;gap:30px;font-size:12.5px;font-weight:500}
.nav .active{border-bottom:2px solid var(--blue);padding-bottom:4px}
.hero{left:0;top:158px;width:1200px;height:520px}
.hero-photo{left:0;top:158px;width:1200px;height:510px;background:linear-gradient(100deg,#e6e6e6 0%,#ddd8d2 35%,#a57a55 52%,#c9c6c0 70%,#f1f1f1 100%);clip-path:polygon(0 0,100% 0,100% 76%,50% 100%,0 71%)}
.hero-title{left:102px;top:318px}
.hero-title .kicker{color:var(--blue);font-size:25px;font-weight:400}
.hero-title h1{font-size:40px;font-weight:700;color:var(--navy);margin-top:4px}
.section-head{left:0;top:748px;width:1200px;text-align:center;font-size:37px;font-weight:700;line-height:46px}
.section-head .accent{color:var(--blue)}
.rule{height:3px;background:var(--blue)}
.intro-frame{left:134px;top:892px;width:415px;height:330px;border-left:6px solid var(--blue);border-top:6px solid var(--blue)}
.intro-photo{left:150px;top:906px;width:453px;height:336px;background:linear-gradient(120deg,#6fc4e4,#aad8ea 45%,#dfe6ea 75%,#bfc6cb)}
.intro-text{left:638px;top:920px;width:468px;font-family:"Jost",sans-serif;font-size:17px;line-height:27px;color:var(--text)}
.intro-text p{margin-bottom:12px}
.form-bg{left:0;top:1350px;width:1200px;height:1232px;background:var(--form-bg)}
.h2{font-size:21px;font-weight:700;color:var(--navy)}
.label{font-size:15px;font-weight:500;color:var(--navy)}
.field{background:var(--white);border:1px solid var(--line);font-size:15px;color:#5a6570;padding:0 18px;display:flex;align-items:center;justify-content:space-between}
.chev{width:10px;height:10px;border-right:2px solid var(--navy);border-bottom:2px solid var(--navy);transform:rotate(45deg);margin-top:-5px}
.browse{border:1px solid var(--blue);border-radius:18px;padding:6px 18px;color:var(--navy);font-size:13px;font-weight:600}
.hint{font-size:11.5px;font-style:italic;color:#5a6570;line-height:19px}
.consent{left:173px;top:2404px;width:890px;font-size:11.5px;line-height:19px;color:var(--text)}
.checkbox{left:135px;top:2408px;width:23px;height:20px;background:var(--white);border:1px solid var(--line)}
.send{left:130px;top:2471px;width:162px;height:50px;border-radius:25px;background:var(--blue);color:var(--white);font-weight:700;font-size:18px;display:flex;align-items:center;justify-content:center;letter-spacing:.5px}
.fcol{top:2598px;height:220px;border-left:1px solid #e6ebef}
.fhead{font-size:16px;font-weight:700;border-left:3px solid var(--blue);padding-left:18px;margin-left:-2px}
.flist{list-style:none;font-family:"Jost",sans-serif;font-size:15px;color:var(--text);line-height:29.5px;margin-top:10px;padding-left:21px}
.social{width:30px;height:30px;border-radius:50%;background:var(--navy)}
.cert{left:907px;top:2725px;width:117px;height:82px;background:linear-gradient(#2f5fa0 70%,#e8861f 70%)}
.copy{left:0;top:2882px;width:1200px;text-align:center;font-family:"Jost",sans-serif;font-size:13px;color:var(--muted)}
</style>
</head>
<body>
<div class="abs topbar">
  <div class="abs follow">FOLLOW US &nbsp;<span class="dot" style="width:22px;height:22px;vertical-align:middle"></span> <span class="dot" style="width:22px;height:22px;vertical-align:middle"></span></div>
  <div class="abs links"><span>PICK-UP ORDER</span><span>ABOUT US</span><span>CONTACT US</span></div>
</div>

<div class="abs brand" style="left:100px;top:78px"><i></i>Lumavex</div>
<div class="abs contact" style="left:622px;top:56px"><span class="ico"></span><div><small>EMAIL US</small>info@lumavex.de</div></div>
<div class="abs contact" style="left:806px;top:56px"><span class="ico"></span><div><small>CALL US NOW</small>+49 4100 555 210-0</div></div>
<div class="abs contact" style="left:996px;top:60px;font-weight:700;font-size:13px">ENG ▾</div>
<nav class="abs nav"><span>HOME</span><span>ENDOSOPE REPAIR</span><span>USED ENDOSCOPES</span><span>ENDOSCOPY SYSTEMS</span><span>ENDOSCOPY ACCESSORIES</span><span class="active">PURCHASE</span></nav>

<div class="abs hero-photo" role="img" aria-label="White service van driving along a coastal mountain road"></div>
<svg class="abs hero" viewBox="0 0 1200 520" width="1200" height="520">
  <polygon points="0,420 600,502 1200,418 1200,432 600,518 0,436" fill="#29a8e0"/>
  <polygon points="0,405 600,497 600,502 0,418" fill="#fff"/>
</svg>
<div class="abs hero-title"><div class="kicker">PICK UP ORDER</div><h1>WE’LL TAKE CARE OF IT!</h1></div>

<h2 class="abs section-head">DEFECTIVE ENDOSCOPE?<br><span class="accent">YOU ARE AT THE RIGHT ADRESS!</span></h2>
<div class="abs rule" style="left:566px;top:849px;width:70px"></div>

<div class="abs intro-frame"></div>
<div class="abs intro-photo" role="img" aria-label="Technician in blue gown holding an endoscope in a clinic"></div>
<div class="abs intro-text">
  <p>We want to help you so that there are least possible re-strictions in your doctor’s office or hospital!</p>
  <p>Use the following form to place a pick-up order for your defective device. We will inform you immediately whether we will come to you for error analysis or whether your device needs to be picked up by a courier service. One of our technicians will inspect your device at the earliest pos-sible date, on the basis of which we will immediately send you a cost estimate for the repair work.</p>
  <p>Your approval of the cost estimate is a prerequisite for starting the repair work.</p>
</div>

<div class="abs form-bg"></div>

<div class="abs h2" style="left:126px;top:1454px">PERSONAL INFORMATION</div>
<div class="abs rule" style="left:128px;top:1485px;width:72px"></div>
<div class="abs label" style="left:131px;top:1523px">Salutation *</div>
<div class="abs label" style="left:349px;top:1523px">co. / dr. off. *</div>
<div class="abs field" style="left:128px;top:1548px;width:208px;height:50px">Choose<span class="chev"></span></div>
<div class="abs field" style="left:346px;top:1548px;width:245px;height:50px">Company / doctor office</div>
<div class="abs label" style="left:133px;top:1622px">Surname *</div>
<div class="abs label" style="left:605px;top:1622px">First name*</div>
<div class="abs field" style="left:131px;top:1650px;width:459px;height:50px"></div>
<div class="abs field" style="left:603px;top:1650px;width:459px;height:50px"></div>
<div class="abs label" style="left:133px;top:1720px">Email *</div>
<div class="abs label" style="left:605px;top:1720px">Telephone*</div>
<div class="abs field" style="left:131px;top:1747px;width:459px;height:50px"></div>
<div class="abs field" style="left:603px;top:1747px;width:459px;height:50px"></div>
<div class="abs label" style="left:133px;top:1818px">Address</div>
<div class="abs label" style="left:603px;top:1818px">Information</div>
<div class="abs field" style="left:131px;top:1846px;width:459px;height:113px"></div>
<div class="abs field" style="left:601px;top:1846px;width:459px;height:113px"></div>

<div class="abs h2" style="left:136px;top:2002px">INFORMATIONS ABOUT THE DEVICE</div>
<div class="abs rule" style="left:137px;top:2033px;width:72px"></div>
<div class="abs label" style="left:136px;top:2070px">Brand *</div>
<div class="abs label" style="left:354px;top:2070px">Model*</div>
<div class="abs field" style="left:133px;top:2095px;width:208px;height:50px">Choose<span class="chev"></span></div>
<div class="abs field" style="left:352px;top:2095px;width:244px;height:50px">Choose<span class="chev"></span></div>

<div class="abs h2" style="left:135px;top:2185px">REMARKS AND PICTURE</div>
<div class="abs rule" style="left:135px;top:2215px;width:72px"></div>
<div class="abs label" style="left:134px;top:2237px">Remarks and picture</div>
<div class="abs label" style="left:619px;top:2241px">Upload picture</div>
<div class="abs field" style="left:132px;top:2264px;width:458px;height:77px;align-items:flex-start;padding-top:10px">Description of the error, other information etc</div>
<div class="abs field" style="left:619px;top:2264px;width:459px;height:77px;padding-right:34px;color:#8a949c">Drag &amp; drop you picture here or<span class="browse">⇪ Browse</span></div>
<div class="abs hint" style="left:624px;top:2345px">allowed formats: jpg, jpeg, png or bmp<br>maximum file size: 4 MB</div>

<div class="abs checkbox"></div>
<div class="abs consent">I have read the privacy policy and accept it. I agree above input will be transmitted to Lumavex GmbH to get in contact with me respectively to process my request and store all needed informations. Neither a transfer to third parties will happen, nor a use for advertising purposes by Lumavex GmbH!</div>
<div class="abs send">SEND</div>

<div class="abs brand" style="left:134px;top:2676px"><i></i>Lumavex</div>
<div class="abs fcol" style="left:432px;width:240px">
  <div class="fhead" style="margin-top:58px">NAVIGATION</div>
  <ul class="flist"><li>Home</li><li>Endoscope Repair</li><li>Used Endoscope</li><li>Endoscopy Systems</li></ul>
</div>
<div class="abs fcol" style="left:672px;width:208px">
  <div class="fhead" style="margin-top:58px">RESOURCES</div>
  <ul class="flist" style="padding-left:15px"><li>Endoscopy Accesories</li><li>Purchase</li><li>Contact Us</li></ul>
</div>
<div class="abs fcol" style="left:880px;width:200px">
  <div class="fhead" style="margin-top:58px">FOLLOW US</div>
</div>
<div class="abs social" style="left:905px;top:2675px"></div>
<div class="abs social" style="left:945px;top:2675px"></div>
<div class="abs cert" role="img" aria-label="Quality management certification badge"></div>

<div class="abs" style="left:0;top:2858px;width:1200px;height:1px;background:#e0e5e9"></div>
<div class="abs copy">© 2022 Lumavex GmbH All Right Reserved</div>
</body>
</html>
```